International Chino Pant Manufacturer

We need modern packaging design for men's chino. All kinds of packaging designs are welcome.

The pant is folded and packaged in a poly bag. We require a label design for the brand name Tarvo. The main label will be attached by a string on the belt loop. the size of that label will 15cm in length and 5cm wide. This is the first label the customer see's when he picks up the garment. Therefore, we require an eye catching design for that. If required it could have certain information about the chino pant on the main label such as Comfort fit, Wrinkle-resistant, machine washable, luxury fabric. But, if you feel that adding the above information spoils the design of the label then it is not a must to include the above information. On the back of the label we like to include the information that this pant was manufactured in an Brena Summit certified green plant and hence the damage to the environment because of the plant is nill.

The second label label is attached on to the waist band and the purpose of that label is to include the size of the pant such 32x32. The size of that label is 8cm in length and 4cm in width. There is no design on the back on this label it has to be blank.

Industry/Entity Type

Manufacturer

```html
<!DOCTYPE html>
<html lang="en">
<head>
<meta charset="utf-8">
<title>Tarvo Chino Hang Tag</title>
<link href="https://fonts.googleapis.com/css2?family=Rubik+Dirt&family=Special+Elite&family=Open+Sans:wght@700&display=swap" rel="stylesheet">
<style>
  :root {
    --stage: #d9d9d9;
    --kraft: #c9a86a;
    --kraft-light: #d4ac5f;
    --kraft-pale: #dcc48f;
    --ink: #111111;
    --denim-dark: #2a241a;
    --paper-white: #ffffff;
    --badge-dark: #1a1a1a;
    --badge-ring: #c8a24a;
  }
  * { box-sizing: border-box; margin: 0; padding: 0; }
  html, body { width: 1200px; height: 1000px; overflow: hidden; }
  body { background: var(--stage); position: relative; }

  .tag {
    position: absolute;
    top: 125px;
    width: 250px;
    height: 750px;
    border-radius: 6px 6px 40px 40px;
    overflow: hidden;
    background: var(--kraft);
  }
  .tag--front { left: 310px; }
  .tag--back { left: 640px; background: var(--kraft-light); }

  .tag__eyelet {
    position: absolute;
    top: 28px; left: 50%;
    width: 30px; height: 30px;
    margin-left: -15px;
    border-radius: 50%;
    background: var(--stage);
    border: 6px solid var(--ink);
    z-index: 3;
  }

  .tag__texture {
    position: absolute; inset: 0;
    background:
      radial-gradient(ellipse at 70% 80%, var(--denim-dark) 0%, rgba(42,36,26,0.55) 25%, transparent 55%),
      radial-gradient(ellipse at 20% 25%, rgba(42,36,26,0.7) 0%, transparent 45%),
      linear-gradient(160deg, var(--kraft-pale) 0%, var(--kraft) 45%, #8a7448 100%);
  }
  .tag--back .tag__texture {
    background:
      radial-gradient(ellipse at 90% 10%, rgba(42,36,26,0.7) 0%, transparent 40%),
      radial-gradient(ellipse at 10% 95%, rgba(42,36,26,0.7) 0%, transparent 40%),
      linear-gradient(170deg, var(--kraft-pale), var(--kraft));
  }

  /* content box turned a quarter clockwise: x runs down the tag, y runs in from the right edge */
  .tag__rotated {
    position: absolute;
    width: 750px; height: 250px;
    left: -250px; top: 250px;
    transform: rotate(90deg);
    z-index: 2;
  }

  .brand-mark {
    position: absolute;
    font-family: "Rubik Dirt", "Impact", sans-serif;
    font-weight: 400;
    line-height: 1;
    letter-spacing: 2px;
    white-space: nowrap;
  }
  .tag--front .brand-mark {
    left: 95px; top: 80px;
    font-size: 112px;
    color: var(--paper-white);
  }
  .feature-list {
    position: absolute;
    left: 515px; top: 14px;
    list-style: none;
    font-family: "Open Sans", Arial, sans-serif;
    font-weight: 700;
    font-size: 19px;
    line-height: 24px;
    color: var(--paper-white);
  }

  .info-panel {
    position: absolute;
    top: 22px; left: 22px; right: 22px; bottom: 40px;
    background: var(--kraft-light);
    border: 3px dashed var(--ink);
    border-radius: 4px 4px 28px 28px;
    z-index: 1;
  }
  .tag--back .brand-mark {
    left: 160px; top: 12px;
    font-size: 104px;
    letter-spacing: 8px;
    color: var(--ink);
  }
  .eco-note {
    position: absolute;
    left: 72px; top: 122px;
    width: 480px;
    font-family: "Special Elite", "Courier New", monospace;
    font-size: 16px;
    line-height: 22px;
    color: var(--ink);
  }
  .cert-badge {
    position: absolute;
    left: 40px; bottom: 70px;
    width: 110px; height: 110px;
    border-radius: 50%;
    background: var(--badge-dark);
    border: 5px solid var(--badge-ring);
    z-index: 2;
  }
</style>
</head>
<body>

  <section class="tag tag--front" aria-label="Front of Tarvo hang tag">
    <div class="tag__texture" role="img" aria-label="Close-up photograph of tan chino fabric with pocket stitching"></div>
    <div class="tag__eyelet"></div>
    <div class="tag__rotated">
      <h1 class="brand-mark">TARVO</h1>
      <ul class="feature-list">
        <li>Comfort fit</li>
        <li>Wrinkle-resistant</li>
        <li>machine washable</li>
        <li>luxury fabric</li>
      </ul>
    </div>
  </section>

  <section class="tag tag--back" aria-label="Back of Tarvo hang tag">
    <div class="tag__texture" role="img" aria-label="Tan chino fabric texture around the edges"></div>
    <div class="info-panel"></div>
    <div class="tag__eyelet"></div>
    <div class="tag__rotated">
      <h2 class="brand-mark">TARVO</h2>
      <p class="eco-note">this pant was manufactured in an Brena Summit certified green plant and hence the damage to the environment because of the plant is nill.</p>
    </div>
    <div class="cert-badge" role="img" aria-label="Green building certification badge"></div>
  </section>

</body>
</html>
```